Dental Savings Plan - Raymond Castell DDS

We need a tri-fold brochure and 1 page flyer/poster for Dr. Raymond Castell' dental office located on Maui, Hawaii. We are offering a new "Dental Savings Plan" to patients.
I have included 3 photos, along with the office logo. You do not have to use all photos if you do not want to. We want this to catch the eyes of patients, easy for them to read and understand, and to show them that this is a much better option than dental insurance.
Please use same Hawaiian theme and colors on the office website https://www.brightcoveclinic.com .

Please also include the following to promote this new plan:

Dental Services Include
• Professional Dental Cleanings (2 per benefit year)
• Perio Maintenance Cleanings (3 per benefit year) covered at 80%
• Radiographs as needed (1 set of X-rays per benefit year)
• Doctor Examinations (2 per benefit year)
• Ozone Treatment
• BRISK Amalgam Removal
• Additional limited/emergency exam (1 per benefit year)
• Cosmetic consultation
• 15% discount on all other services (including cosmetic procedures)
• 10% discount on implants and implant crowns

Advantages of the Dental Savings Plan
1. No deductibles
2. No waiting periods
3. No claims to file
4. No frequency limitations or exclusions
5. No yearly maximum benefits
6. No pre-authorization requirements
7. No pre-existing conditions limitations
8. State of the art facility and technology
9. Immediate enrollment
10. Highest quality of care for you and your Ohana

Annual Fee
$399 first family member/individual (equivalent to $33 per month)
$349 second family member (equivalent to $29 per month)
$249 each additional family member (equivalent to $20 per month)

Provisions of the Dental Savings Plan
• May not be combined with insurance plans, discounts or promotions
• This Dental Savings Plan is not an insurance plan, but a payment arrangement provided by Raymond Castell DDS, and is not transferable to any other dental office or dental specialist
• Payment for services are due at the date of service
• This program is for you and is not transferable
• Benefits are provided for one year from the date the plan is purchased
• Must be paid in full when starting the plan
• No refunds will be provided for dues of the plan annual fee under any circumstances, including failure to schedule and maintain appointments
• If Pay Ladder is used to pay for the program and for services then only a 10% discount will be given
• To receive the full 15% discount on restorative treatment, you must schedule the appointment the day it is recommended. Any failed appointment results in the loss of the 15% discount.

Target Market(s)

Dental patients without dental insurance

Industry/Entity Type

Dental Clinic

Requirements
Must have
• My project must have the logo file to identify the dental office, Hawaiian theme, same colors as website, match style of website font, theme and colors, as well as, all the Dental Services, Advantages of the Dental Savings Plan, Annual Fee, and the Provisions of the Dental Savings Plan.

```html
<!DOCTYPE html>
<html lang="en">
<head>
<meta charset="utf-8">
<title>Dental Savings Plan – Palekai Smile Studio</title>
<link rel="stylesheet" href="https://fonts.googleapis.com/css2?family=Open+Sans:wght@400;600;700&family=Playfair+Display:wght@900&display=swap">
<style>
  :root {
    --green: #8cc63f;
    --green-dark: #6db33f;
    --green-title: #7dbb2f;
    --blue: #2f9bd5;
    --blue-deep: #1b86c4;
    --blue-light: #5cc3ef;
    --white: #ffffff;
    --hero-cool: #a9b6bd;
    --hero-warm: #e2cfbf;
  }
  * { box-sizing: border-box; margin: 0; padding: 0; }
  html, body { width: 927px; height: 1200px; overflow: hidden; background: var(--white); }
  body { font-family: "Open Sans", Arial, sans-serif; color: var(--white); }

  .flyer { position: relative; width: 927px; height: 1200px; overflow: hidden; background: var(--white); }

  /* Hero */
  .hero-photo {
    position: absolute; left: 0; top: 0; width: 927px; height: 350px;
    background: linear-gradient(100deg, #7f8f99 0%, #93a1a9 30%, var(--hero-cool) 52%, #cbc7c1 66%, var(--hero-warm) 80%, #d3ad92 100%);
  }
  .hero-curve { position: absolute; left: 0; top: 300px; width: 927px; height: 60px; }

  .brand { position: absolute; left: 14px; top: 28px; width: 230px; text-align: center; }
  .brand-mark { display: block; width: 44px; height: 44px; border-radius: 50%; background: var(--green); margin: 40px auto 14px; }
  .brand-name { font-size: 16px; font-weight: 600; color: var(--white); letter-spacing: .3px; }

  .title {
    position: absolute; left: 290px; top: 68px; width: 340px; text-align: center;
    font-family: "Playfair Display", Georgia, serif; font-weight: 900; font-size: 43px; line-height: 48px;
    color: var(--green-title); text-shadow: 2px 3px 4px rgba(0,0,0,.35); letter-spacing: .5px;
  }

  .fee { position: absolute; left: 22px; top: 198px; }
  .fee-heading { font-size: 24px; font-weight: 700; color: var(--green); letter-spacing: .3px; margin-bottom: 8px; }
  .fee-list { list-style: none; }
  .fee-list li { display: flex; align-items: center; font-size: 16px; line-height: 25px; color: var(--white); text-shadow: 0 1px 2px rgba(0,0,0,.3); }
  .fee-list li svg { margin-right: 9px; flex: none; }
  .fee-list b { font-weight: 700; margin-right: 5px; }

  /* Columns */
  .column {
    position: absolute; top: 470px; height: 565px; border-radius: 12px;
    background: linear-gradient(180deg, var(--blue) 0%, var(--blue-deep) 100%);
    box-shadow: 0 6px 10px rgba(0,0,0,.18);
  }
  .column-services { left: 17px; width: 287px; }
  .column-advantages { left: 317px; width: 287px; }
  .column-provisions { left: 620px; width: 288px; }

  .badge { position: absolute; top: 413px; width: 114px; height: 114px; border-radius: 50%;
    background: var(--green); padding: 5px; }
  .badge-inner { width: 100%; height: 100%; border-radius: 50%; border: 4px solid var(--white);
    background: radial-gradient(circle at 50% 35%, var(--blue-light), var(--blue-deep));
    display: flex; align-items: center; justify-content: center; }
  .badge-services { left: 103px; }
  .badge-advantages { left: 403px; }
  .badge-provisions { left: 707px; }

  .column-heading { position: absolute; top: 64px; left: 0; right: 0; text-align: center;
    font-size: 21px; font-weight: 600; line-height: 30px; letter-spacing: .2px; }

  .services-list { position: absolute; top: 140px; left: 18px; right: 8px; list-style: none; font-size: 14.5px; line-height: 18.3px; }
  .services-list li::before { content: "• "; }
  .services-list .note { display: block; font-size: 10.5px; line-height: 18.3px; padding-left: 14px; }
  .services-list .note-strong { font-size: 14.5px; }

  .discounts { position: absolute; top: 409px; left: 16px; display: flex; gap: 10px; }
  .discount { width: 124px; height: 77px; border: 2px solid var(--green); text-align: center; padding-top: 12px; }
  .discount-rate { font-size: 16px; line-height: 20px; }
  .discount-detail { font-size: 10px; line-height: 13px; }
  .discount-detail small { font-size: 7.5px; display: block; }

  .advantages-list { position: absolute; top: 142px; left: 12px; right: 8px; list-style: none; font-size: 14px; line-height: 30px; }
  .advantages-list li { display: flex; align-items: flex-start; }
  .advantages-list li svg { flex: none; margin: 9px 8px 0 0; }

  .provisions-list { position: absolute; top: 139px; left: 10px; right: 10px; list-style: none;
    font-size: 12.4px; line-height: 14.6px; text-align: justify; hyphens: auto; }
  .provisions-list li { margin-bottom: 5.5px; }
  .provisions-list li::before { content: "• "; color: var(--green); font-weight: 700; }

  /* Lower photo */
  .care-photo { position: absolute; left: -22px; top: 955px; width: 262px; height: 262px; border-radius: 50%;
    border: 5px solid var(--white); z-index: 2;
    background: radial-gradient(circle at 45% 45%, #f1e3da 0%, #dcc3b6 45%, #b9ccd6 80%, #a8bfcc 100%); }

  /* Footer */
  .footer { position: absolute; left: 0; top: 1094px; width: 927px; height: 106px;
    background: linear-gradient(90deg, var(--green-dark), var(--green)); }
  .contact { position: absolute; right: 16px; top: 15px; list-style: none; text-align: right; font-size: 15px; line-height: 26.5px; color: var(--white); }
  .contact li { display: flex; justify-content: flex-end; align-items: center; }
  .contact li svg { margin-left: 10px; flex: none; }
  .contact .sep { margin: 0 9px; }
</style>
</head>
<body>
<main class="flyer">

  <div class="hero-photo" role="img" aria-label="Photo of a smiling young woman with long brown hair against a soft, blurred city background"></div>
  <svg class="hero-curve" viewBox="0 0 927 60" preserveAspectRatio="none" aria-hidden="true">
    <path d="M0 0 Q 470 70 927 0 L927 60 L0 60 Z" fill="#ffffff"/>
    <path d="M0 14 Q 470 64 927 6 L927 18 Q 470 72 0 24 Z" fill="#8cc63f"/>
  </svg>

  <div class="brand">
    <span class="brand-mark" aria-hidden="true"></span>
    <span class="brand-name">Palekai Smile Studio</span>
  </div>

  <h1 class="title">DENTAL<br>SAVINGS PLAN</h1>

  <section class="fee">
    <h2 class="fee-heading">ANNUAL FEE</h2>
    <ul class="fee-list">
      <li><svg width="12" height="12" viewBox="0 0 12 12"><circle cx="6" cy="6" r="5" fill="none" stroke="#8cc63f" stroke-width="1.4"/><path d="M3.5 6 L5.3 7.8 L8.6 4.3" fill="none" stroke="#8cc63f" stroke-width="1.4"/></svg><b>$399</b> first family member/individual (equivalent to $33 per month)</li>
      <li><svg width="12" height="12" viewBox="0 0 12 12"><circle cx="6" cy="6" r="5" fill="none" stroke="#8cc63f" stroke-width="1.4"/><path d="M3.5 6 L5.3 7.8 L8.6 4.3" fill="none" stroke="#8cc63f" stroke-width="1.4"/></svg><b>$349</b> second family member (equivalent to $29 per month)</li>
      <li><svg width="12" height="12" viewBox="0 0 12 12"><circle cx="6" cy="6" r="5" fill="none" stroke="#8cc63f" stroke-width="1.4"/><path d="M3.5 6 L5.3 7.8 L8.6 4.3" fill="none" stroke="#8cc63f" stroke-width="1.4"/></svg><b>$249</b> each additional family member (equivalent to $20 per month)</li>
    </ul>
  </section>

  <section class="column column-services">
    <h2 class="column-heading">DENTAL SERVICES<br>INCLUDE</h2>
    <ul class="services-list">
      <li>Professional Dental Cleanings<span class="note">(2 per benefit year)</span></li>
      <li>Perio Maintenance Cleanings<span class="note">(3 per benefit year) <span class="note-strong">covered at 80%</span></span></li>
      <li>Radiographs as needed<span class="note">(1 set of X-rays per benefit year)</span></li>
      <li>Doctor Examinations<span class="note">(2 per benefit year)</span></li>
      <li>Ozone Treatment</li>
      <li>BRISK Amalgam Removal</li>
      <li>Additional limited/emergency exam<span class="note">(1 per benefit year)</span></li>
      <li>Cosmetic consultation</li>
    </ul>
    <div class="discounts">
      <div class="discount">
        <div class="discount-rate">15% discount</div>
        <div class="discount-detail">on all other services<small>(including cosmetic procedures)</small></div>
      </div>
      <div class="discount">
        <div class="discount-rate">10% discount</div>
        <div class="discount-detail">on implants and<br>implant crowns</div>
      </div>
    </div>
  </section>

  <section class="column column-advantages">
    <h2 class="column-heading">ADVANTAGES OF THE<br>DENTAL SAVINGS PLAN</h2>
    <ul class="advantages-list">
      <li><svg width="11" height="11" viewBox="0 0 12 12"><circle cx="6" cy="6" r="5" fill="none" stroke="#8cc63f" stroke-width="1.4"/><path d="M3.5 6 L5.3 7.8 L8.6 4.3" fill="none" stroke="#8cc63f" stroke-width="1.4"/></svg>No deductibles</li>
      <li><svg width="11" height="11" viewBox="0 0 12 12"><circle cx="6" cy="6" r="5" fill="none" stroke="#8cc63f" stroke-width="1.4"/><path d="M3.5 6 L5.3 7.8 L8.6 4.3" fill="none" stroke="#8cc63f" stroke-width="1.4"/></svg>No waiting periods</li>
      <li><svg width="11" height="11" viewBox="0 0 12 12"><circle cx="6" cy="6" r="5" fill="none" stroke="#8cc63f" stroke-width="1.4"/><path d="M3.5 6 L5.3 7.8 L8.6 4.3" fill="none" stroke="#8cc63f" stroke-width="1.4"/></svg>No claims to file</li>
      <li><svg width="11" height="11" viewBox="0 0 12 12"><circle cx="6" cy="6" r="5" fill="none" stroke="#8cc63f" stroke-width="1.4"/><path d="M3.5 6 L5.3 7.8 L8.6 4.3" fill="none" stroke="#8cc63f" stroke-width="1.4"/></svg><span>No frequency limitations or<br>exclusions</span></li>
      <li><svg width="11" height="11" viewBox="0 0 12 12"><circle cx="6" cy="6" r="5" fill="none" stroke="#8cc63f" stroke-width="1.4"/><path d="M3.5 6 L5.3 7.8 L8.6 4.3" fill="none" stroke="#8cc63f" stroke-width="1.4"/></svg>No yearly maximum benefits</li>
      <li><svg width="11" height="11" viewBox="0 0 12 12"><circle cx="6" cy="6" r="5" fill="none" stroke="#8cc63f" stroke-width="1.4"/><path d="M3.5 6 L5.3 7.8 L8.6 4.3" fill="none" stroke="#8cc63f" stroke-width="1.4"/></svg>No pre-authorization requirements</li>
      <li><svg width="11" height="11" viewBox="0 0 12 12"><circle cx="6" cy="6" r="5" fill="none" stroke="#8cc63f" stroke-width="1.4"/><path d="M3.5 6 L5.3 7.8 L8.6 4.3" fill="none" stroke="#8cc63f" stroke-width="1.4"/></svg>No pre-existing conditions limitations</li>
      <li><svg width="11" height="11" viewBox="0 0 12 12"><circle cx="6" cy="6" r="5" fill="none" stroke="#8cc63f" stroke-width="1.4"/><path d="M3.5 6 L5.3 7.8 L8.6 4.3" fill="none" stroke="#8cc63f" stroke-width="1.4"/></svg>State of the art facility &amp; technology</li>
      <li><svg width="11" height="11" viewBox="0 0 12 12"><circle cx="6" cy="6" r="5" fill="none" stroke="#8cc63f" stroke-width="1.4"/><path d="M3.5 6 L5.3 7.8 L8.6 4.3" fill="none" stroke="#8cc63f" stroke-width="1.4"/></svg>Immediate enrollment</li>
      <li><svg width="11" height="11" viewBox="0 0 12 12"><circle cx="6" cy="6" r="5" fill="none" stroke="#8cc63f" stroke-width="1.4"/><path d="M3.5 6 L5.3 7.8 L8.6 4.3" fill="none" stroke="#8cc63f" stroke-width="1.4"/></svg><span>Highest quality of care for you and<br>your Ohana</span></li>
    </ul>
  </section>

  <section class="column column-provisions">
    <h2 class="column-heading">PROVISIONS OF THE<br>DENTAL SAVINGS PLAN</h2>
    <ul class="provisions-list">
      <li>May not be combined with insurance plans, discounts or promotions</li>
      <li>This Dental Savings Plan is not an insurance plan, but a payment arrangement provided by Raymond Castell DDS, and is not transferable to any other dental office or dental specialist</li>
      <li>Payment for services are due at the date of service</li>
      <li>This program is for you and is not transferable</li>
      <li>Benefits are provided for one year from the date the plan is purchased</li>
      <li>Must be paid in full when starting the plan</li>
      <li>No refunds will be provided for dues of the plan annual fee under any circumstances, including failure to schedule and maintain appointments</li>
      <li>If Pay Ladder is used to pay for the program and for services no discount will be applied</li>
      <li>To receive the full 15% discount on restor-ative treatment, you must schedule the appointment the day it is recommended. Any failed appointment results in the loss of the 15% discount.</li>
    </ul>
  </section>

  <div class="badge badge-services"><div class="badge-inner">
    <svg width="40" height="46" viewBox="0 0 40 46" aria-hidden="true"><path d="M10 3 C3 3 1 10 3 18 C5 25 6 30 7 38 C8 44 12 44 13 38 C14 32 16 27 20 27 C24 27 26 32 27 38 C28 44 32 44 33 38 C34 30 35 25 37 18 C39 10 37 3 30 3 C26 3 24 5 20 5 C16 5 14 3 10 3 Z" fill="none" stroke="#fff" stroke-width="2.4" stroke-linejoin="round"/><path d="M9 10 Q10 7 13 7" fill="none" stroke="#fff" stroke-width="2"/></svg>
  </div></div>
  <div class="badge badge-advantages"><div class="badge-inner">
    <svg width="52" height="40" viewBox="0 0 52 40" aria-hidden="true"><circle cx="15" cy="22" r="12" fill="#fff"/><text x="15" y="27" text-anchor="middle" font-family="Open Sans, sans-serif" font-size="14" font-weight="700" fill="#1b86c4">$</text><path d="M32 10 A13 13 0 1 0 45 23 L32 23 Z" fill="#fff"/><path d="M35 7 A13 13 0 0 1 48 20 L35 20 Z" fill="#fff"/></svg>
  </div></div>
  <div class="badge badge-provisions"><div class="badge-inner">
    <svg width="40" height="40" viewBox="0 0 40 40" aria-hidden="true"><circle cx="10" cy="10" r="6" fill="none" stroke="#fff" stroke-width="3"/><circle cx="30" cy="30" r="6" fill="none" stroke="#fff" stroke-width="3"/><line x1="32" y1="4" x2="8" y2="36" stroke="#fff" stroke-width="3.5" stroke-linecap="round"/></svg>
  </div></div>

  <div class="care-photo" role="img" aria-label="Photo of a patient smiling during a dental check-up with a dentist's mirror and probe"></div>

  <footer class="footer">
    <ul class="contact">
      <li>808-555-0142
        <svg width="18" height="18" viewBox="0 0 18 18"><circle cx="9" cy="9" r="8" fill="none" stroke="#fff" stroke-width="1.5"/><path d="M6 5 L7.5 5 L8.2 7 L7.2 7.8 Q8 9.8 10.2 10.8 L11 9.8 L13 10.5 L13 12 Q12.5 13 11 13 Q6 12 5 7 Q5 5.5 6 5 Z" fill="#fff"/></svg>
      </li>
      <li>www.brightcoveclinic.com<span class="sep">|</span>hello@palekaismile.com
        <svg width="18" height="18" viewBox="0 0 18 18"><circle cx="9" cy="9" r="8" fill="none" stroke="#fff" stroke-width="1.5"/><circle cx="9" cy="9" r="2.3" fill="none" stroke="#fff" stroke-width="1.4"/><path d="M11.3 7 L11.3 10 Q11.3 11.5 12.7 11 Q13.5 10 13.3 8.5 A4.4 4.4 0 1 0 11 12.8" fill="none" stroke="#fff" stroke-width="1.3"/></svg>
      </li>
      <li>4470 Makai Rd # 112, Lanikoa, HI 96799
        <svg width="18" height="18" viewBox="0 0 18 18"><circle cx="9" cy="9" r="8" fill="none" stroke="#fff" stroke-width="1.5"/><path d="M9 14 Q5.5 9.5 5.5 7.5 A3.5 3.5 0 0 1 12.5 7.5 Q12.5 9.5 9 14 Z" fill="#fff"/><circle cx="9" cy="7.5" r="1.3" fill="#7dbb2f"/></svg>
      </li>
    </ul>
  </footer>

</main>
</body>
</html>
```